Brightway Carpet and Tile cleaning Business card Design

I need a design that has the same feel as my van.
i would also like a prominent "Review us on facebook" somewhere, but not that it makes it look silly.
I would like the card to have a little bit of grey or black in the design as well.

It will need contact details
phone: 0455 817264
email: rkbrightwayclean@mailbox-example.com
website: www.brightwaycarpetandtilecleaning-example.com.au
facebook: /brightwaycarpetandtilecleaning

Industry/Entity Type

Business

Contact Information for Business Card

Phone number 0455817264
Email rkbrightwayclean@mailbox-example.com
Website www.brightwaycarpetandtilecleaning-example.com.au
Facebook/brightwaycarpetandtilecleaning

Colors
000000

Requirements
Must have
• Same feel as my van
• I want the card to stand out from the crowd
Nice to have
• Maybe include a tiny bit of a third colour? Grey's,blacks, orange?

```html
<!DOCTYPE html>
<html lang="en">
<head>
<meta charset="utf-8">
<title>Brightway Carpet and Tile cleaning – Business Card</title>
<link href="https://fonts.googleapis.com/css2?family=Montserrat:wght@500;600;700&display=swap" rel="stylesheet">
<style>
  :root {
    --stage: #2b2b2d;
    --card: #1e2225;
    --card-tone: #252a2e;
    --cyan: #1fa9dc;
    --green: #8dc63f;
    --grey: #9a9ea2;
    --ink-dark: #1e2225;
  }
  * { box-sizing: border-box; margin: 0; padding: 0; }
  html, body {
    width: 1200px; height: 1189px; overflow: hidden;
    background: var(--stage);
    font-family: "Montserrat", Arial, sans-serif;
  }
  .card {
    position: absolute; left: 130px;
    width: 940px; height: 520px;
    border-radius: 22px;
    background: var(--card);
    overflow: hidden;
  }
  .card--front { top: 40px; }
  .card--back { top: 625px; }
  .card__texture {
    position: absolute; inset: 0;
    background: radial-gradient(ellipse at 60% 40%, var(--card-tone), var(--card) 70%);
  }
  .brand {
    position: absolute; display: flex; align-items: center; gap: 16px;
    color: var(--cyan); font-weight: 700; white-space: nowrap;
  }
  .brand__dot {
    width: 34px; height: 34px; border-radius: 50%; background: var(--cyan); flex: none;
  }
  .card--front .brand {
    left: 0; right: 0; top: 225px; justify-content: center; font-size: 38px;
  }
  .card--back .brand { left: 70px; top: 110px; font-size: 30px; }
  .card--back .brand__dot { width: 28px; height: 28px; }
  .person {
    position: absolute; right: 60px; top: 180px; text-align: right;
  }
  .person__name { color: var(--cyan); font-weight: 700; font-size: 26px; line-height: 1.2; }
  .person__role { color: var(--green); font-weight: 500; font-size: 21px; margin-top: 2px; line-height: 1.2; }
  .divider {
    position: absolute; left: 70px; right: 320px; top: 248px;
    height: 2px; background: var(--green);
  }
  .contacts {
    position: absolute; left: 70px; top: 300px; list-style: none;
  }
  .contacts li {
    display: flex; align-items: center; gap: 12px;
    color: var(--cyan); font-size: 23px; font-weight: 500;
    margin-bottom: 12px; white-space: nowrap;
  }
  .contacts__icon {
    width: 32px; height: 32px; border-radius: 5px; background: var(--green);
    flex: none; display: flex; align-items: center; justify-content: center;
  }
</style>
</head>
<body>

  <section class="card card--front">
    <div class="card__texture" role="img" aria-label="Soft dark bubble pattern across the card"></div>
    <div class="brand"><span class="brand__dot"></span>Brightway Carpet and Tile cleaning</div>
  </section>

  <section class="card card--back">
    <div class="card__texture" role="img" aria-label="Soft dark bubble pattern across the card"></div>
    <div class="brand"><span class="brand__dot"></span>Brightway Carpet and Tile cleaning</div>

    <div class="person">
      <p class="person__name">Marco Delvane</p>
      <p class="person__role">Managing/Director</p>
    </div>

    <div class="divider"></div>

    <ul class="contacts">
      <li>
        <span class="contacts__icon">
          <svg width="20" height="20" viewBox="0 0 24 24"><path fill="var(--ink-dark)" d="M6.6 10.8a15 15 0 0 0 6.6 6.6l2.2-2.2c.3-.3.7-.4 1-.2 1.1.4 2.300.6 3.6.6.6 0 1 .4 1 1V20c0 .6-.4 1-1 1A17 17 0 0 1 3 4c0-.6.4-1 1-1h3.5c.6 0 1 .4 1 1 0 1.3.2 2.5.6 3.6.1.3 0 .7-.2 1z"/></svg>
        </span>0455 817264
      </li>
      <li>
        <span class="contacts__icon">
          <svg width="22" height="18" viewBox="0 0 24 18"><rect x="1.5" y="1.5" width="21" height="15" rx="1.5" fill="none" stroke="var(--ink-dark)" stroke-width="2"/><path d="M2 2l10 8 10-8" fill="none" stroke="var(--ink-dark)" stroke-width="2"/></svg>
        </span>rkbrightwayclean@mailbox-example.com
      </li>
      <li>
        <span class="contacts__icon">
          <svg width="20" height="20" viewBox="0 0 24 24" fill="none" stroke="var(--ink-dark)" stroke-width="2"><circle cx="12" cy="12" r="10"/><ellipse cx="12" cy="12" rx="4.5" ry="10"/><path d="M2 12h20"/></svg>
        </span>www.brightwaycarpetandtilecleaning-example.com.au
      </li>
      <li>
        <span class="contacts__icon">
          <svg width="20" height="20" viewBox="0 0 24 24"><path fill="var(--ink-dark)" d="M12 2.5l2.9 6 6.6.9-4.8 4.6 1.2 6.5L12 17.4l-5.9 3.1 1.2-6.5L2.5 9.4l6.6-.9z"/></svg>
        </span>/brightwaycarpetandtilecleaning
      </li>
    </ul>
  </section>

</body>
</html>
```